website update

We need to redesign our current website to be more personalised and sophisticated. We are physiotherapy clinic based in sydney australia, offer a range of clinical service such as Physiotherapy, Massage, sports injuries rehabilitation, Women's health (incontinency etc), Pilates classes, back pain exercise program, acupuncture, Gait analysis.
our current website is www.brightlanehealth.com.au
an example of ideal website is http://quillbrookrehabstudio.com/
homepage: with a revolving displaying attached photos which is linked to relevants page

```html
<!DOCTYPE html>
<html lang="en">
<head>
<meta charset="utf-8">
<title>Brightlane Physiotherapy & Sports Clinic</title>
<link href="https://fonts.googleapis.com/css2?family=Questrial&family=Ubuntu:wght@400;500&display=swap" rel="stylesheet">
<style>
:root{
  --green:#2f9a4c;
  --green-dark:#23803d;
  --green-text:#2e8b45;
  --lime:#c9df80;
  --lime-bar:#8cc63f;
  --cream:#eef2cf;
  --ink:#222;
  --body:#3a3a3a;
  --white:#fff;
}
*{margin:0;padding:0;box-sizing:border-box}
html,body{width:780px;height:1200px;overflow:hidden;background:var(--white)}
body{position:relative;font-family:"Ubuntu",sans-serif;color:var(--body)}
.abs{position:absolute}
h2,h3{font-family:"Questrial",sans-serif;font-weight:400;color:var(--ink)}

.header{left:0;top:0;width:780px;height:65px;background:var(--white)}
.brand{left:78px;top:14px;display:flex;align-items:center;gap:8px}
.brand-mark{width:34px;height:34px;border-radius:50%;background:var(--lime-bar)}
.brand-name{font-size:21px;font-weight:500;color:var(--green-text);line-height:1}
.brand-tag{font-size:7px;color:var(--green-text);letter-spacing:.3px;margin-top:2px}
.clinic{font-size:11px;line-height:1}
.clinic .name{color:var(--green-text);display:flex;align-items:center;gap:4px}
.clinic .num{color:var(--ink);font-size:11px;margin-top:7px;font-weight:500}

.band-top{left:0;top:65px;width:780px;height:178px;background:var(--cream)}
.band-low{left:0;top:243px;width:780px;height:179px;background:var(--lime)}
.nav{left:78px;top:88px;width:624px;height:30px;background:linear-gradient(#46b463,var(--green-dark));display:flex;justify-content:space-around;align-items:center;box-shadow:0 1px 2px rgba(0,0,0,.2)}
.nav a{color:var(--white);font-size:8.5px;text-decoration:none}
.slide{left:78px;top:118px;width:623px;height:268px;background:linear-gradient(120deg,#e4e4e4,#c9c9cc 55%,#b54a78 56%,#c95a88 64%,#d3d3d6 65%,#bdbdc0)}
.caption{right:80px;top:337px;height:30px;padding:0 6px;background:rgba(90,90,90,.35);color:var(--white);font-size:18px;line-height:30px}
.dots{left:365px;top:399px;display:flex;gap:3px}
.dots span{width:7px;height:7px;border-radius:50%;background:#e6eec0;border:1px solid #b9cb7a}
.dots span.on{background:var(--green)}

.welcome h2{font-size:15.5px;line-height:18px}
.intro{font-size:8.2px;line-height:18px;width:300px}
.svc{width:125px;height:23px;background:var(--cream);font-size:8.2px;color:var(--ink);line-height:23px;padding-left:6px}

.video{left:435px;top:442px;width:267px;height:231px;background:#000}
.video-title{left:10px;top:5px;color:var(--white);font-size:8.5px}
.video-frame{left:8px;top:18px;width:251px;height:204px;background:linear-gradient(#d8d8da,#b4b4b7)}
.play{left:111px;top:78px;width:45px;height:40px;background:#111;border-radius:3px}

.col h3{font-size:15px}
.col ul{list-style:none;margin-top:10px}
.col li{font-size:8.5px;line-height:18.3px;color:var(--ink);display:flex;align-items:center;gap:7px}
.tick{width:7px;height:7px;flex:none}
.sub{font-family:"Questrial",sans-serif;color:var(--green-text);font-size:11.5px}
.btn{width:74px;height:28px;border-radius:3px;background:linear-gradient(#43b060,var(--green-dark));color:var(--white);font-size:8.5px;line-height:28px;text-align:center;box-shadow:0 2px 2px rgba(0,0,0,.25)}

.partner{top:966px;height:22px;border-radius:3px}

.footer{left:0;top:1014px;width:780px;height:158px;background:var(--cream)}
.footer h3{font-size:14.5px}
.addr{font-size:9px;line-height:14px;color:var(--ink)}
.addr .city{color:var(--green-text)}
.fphone{font-size:10.5px;color:var(--body);display:flex;align-items:center;gap:6px}
.hours{font-size:9px;line-height:18px;color:var(--ink)}
.appt{left:520px;top:1122px;width:155px;height:30px;background:linear-gradient(#9ed24a,#6aa82a);border:2px solid #e2e8c8;color:var(--white);font-size:10px;line-height:26px;text-align:center;box-shadow:0 1px 3px rgba(0,0,0,.3)}
.copy{left:0;top:1172px;width:780px;height:28px;background:var(--lime-bar);color:var(--white);font-size:7.5px;line-height:28px;padding-left:78px}
</style>
</head>
<body>

<header class="header abs">
  <div class="brand abs">
    <span class="brand-mark"></span>
    <div><div class="brand-name">Brightlane</div><div class="brand-tag">PHYSIOTHERAPY &amp; SPORTS CLINIC</div></div>
  </div>
  <div class="clinic abs" style="left:518px;top:16px">
    <div class="name"><svg width="8" height="10" viewBox="0 0 8 10"><path d="M2 0 L4 2 L3 3.5 Q4 6 5.5 6.8 L6.5 6 L8 8 L6.5 9.8 Q1 8 0 1.5Z" fill="#2e8b45"/></svg>Elmwood clinic</div>
    <div class="num">02 9000 4417</div>
  </div>
  <div class="clinic abs" style="left:629px;top:15px">
    <div class="name"><svg width="8" height="10" viewBox="0 0 8 10"><path d="M2 0 L4 2 L3 3.5 Q4 6 5.5 6.8 L6.5 6 L8 8 L6.5 9.8 Q1 8 0 1.5Z" fill="#2e8b45"/></svg>Harbourside</div>
    <div class="num">02 9000 7623</div>
  </div>
</header>

<div class="band-top abs"></div>
<div class="band-low abs"></div>
<nav class="nav abs">
  <a>Home</a><a>About us</a><a>Common Conditions</a><a>Treatments</a><a>Specialised Services</a><a>OH&amp;S / Workplace Assessment</a><a>Contact Us</a>
</nav>
<div class="slide abs" role="img" aria-label="Physiotherapist guiding a patient through a stretch on reformer equipment"></div>
<div class="caption abs">Proin gravida nibh vel velit auctor aliquet</div>
<div class="dots abs"><span class="on"></span><span></span><span></span><span></span><span></span></div>

<section class="welcome">
  <h2 class="abs" style="left:77px;top:442px">Welcome to Brightlane Spinal &amp; Sports<br>physiotherapy clinic</h2>
  <p class="intro abs" style="left:78px;top:490px">We are physiotherapy clinic based in sydney australia, offer a range of clinical service such as</p>
  <div class="svc abs" style="left:78px;top:539px">Physiotherapy</div>
  <div class="svc abs" style="left:222px;top:539px">Massage</div>
  <div class="svc abs" style="left:78px;top:575px">Sports Injuries Rehabilitation</div>
  <div class="svc abs" style="left:222px;top:575px">Women's Health</div>
  <div class="svc abs" style="left:78px;top:612px">Pilates Classes</div>
  <div class="svc abs" style="left:222px;top:612px">Back Pain Exercise Program</div>
  <div class="svc abs" style="left:78px;top:649px">Acupuncture</div>
  <div class="svc abs" style="left:222px;top:649px">Gait analysis</div>
</section>

<div class="video abs">
  <div class="video-title abs">Sports Injuries rehabilitation</div>
  <div class="video-frame abs" role="img" aria-label="Runner on a treadmill while a physiotherapist observes her gait">
    <div class="play abs"><svg width="45" height="40" viewBox="0 0 45 40"><path d="M18 14 L28 20 L18 26Z" fill="#fff"/></svg></div>
  </div>
</div>

<section class="col abs" style="left:77px;top:708px">
  <h3>We Offer</h3>
  <ul>
    <li><svg class="tick" viewBox="0 0 8 8"><circle cx="4" cy="4" r="4" fill="#8cc63f"/><path d="M3 2 L5 4 L3 6" stroke="#fff" fill="none"/></svg>Manual therapy and spinal manipulation</li>
    <li><svg class="tick" viewBox="0 0 8 8"><circle cx="4" cy="4" r="4" fill="#8cc63f"/><path d="M3 2 L5 4 L3 6" stroke="#fff" fill="none"/></svg>Acupuncture/Dry Needling</li>
    <li><svg class="tick" viewBox="0 0 8 8"><circle cx="4" cy="4" r="4" fill="#8cc63f"/><path d="M3 2 L5 4 L3 6" stroke="#fff" fill="none"/></svg>Electrical Therapy</li>
    <li><svg class="tick" viewBox="0 0 8 8"><circle cx="4" cy="4" r="4" fill="#8cc63f"/><path d="M3 2 L5 4 L3 6" stroke="#fff" fill="none"/></svg>Spinal strengthening</li>
    <li><svg class="tick" viewBox="0 0 8 8"><circle cx="4" cy="4" r="4" fill="#8cc63f"/><path d="M3 2 L5 4 L3 6" stroke="#fff" fill="none"/></svg>Sports Injuries rehabilitation</li>
    <li><svg class="tick" viewBox="0 0 8 8"><circle cx="4" cy="4" r="4" fill="#8cc63f"/><path d="M3 2 L5 4 L3 6" stroke="#fff" fill="none"/></svg>Post Operative rehabilitation</li>
    <li><svg class="tick" viewBox="0 0 8 8"><circle cx="4" cy="4" r="4" fill="#8cc63f"/><path d="M3 2 L5 4 L3 6" stroke="#fff" fill="none"/></svg>Custom-made orthotics</li>
  </ul>
</section>
<div class="btn abs" style="left:78px;top:873px">More Info</div>

<section class="col abs" style="left:316px;top:708px">
  <h3>We Treat</h3>
  <ul>
    <li><svg class="tick" viewBox="0 0 8 8"><circle cx="4" cy="4" r="4" fill="#8cc63f"/><path d="M3 2 L5 4 L3 6" stroke="#fff" fill="none"/></svg>Back and low back pain</li>
    <li><svg class="tick" viewBox="0 0 8 8"><circle cx="4" cy="4" r="4" fill="#8cc63f"/><path d="M3 2 L5 4 L3 6" stroke="#fff" fill="none"/></svg>Neck pain and Headaches</li>
    <li><svg class="tick" viewBox="0 0 8 8"><circle cx="4" cy="4" r="4" fill="#8cc63f"/><path d="M3 2 L5 4 L3 6" stroke="#fff" fill="none"/></svg>Spinal/ Posture disorders</li>
    <li><svg class="tick" viewBox="0 0 8 8"><circle cx="4" cy="4" r="4" fill="#8cc63f"/><path d="M3 2 L5 4 L3 6" stroke="#fff" fill="none"/></svg>Spinal strengthening</li>
    <li><svg class="tick" viewBox="0 0 8 8"><circle cx="4" cy="4" r="4" fill="#8cc63f"/><path d="M3 2 L5 4 L3 6" stroke="#fff" fill="none"/></svg>Sports Injuries rehabilitation</li>
    <li><svg class="tick" viewBox="0 0 8 8"><circle cx="4" cy="4" r="4" fill="#8cc63f"/><path d="M3 2 L5 4 L3 6" stroke="#fff" fill="none"/></svg>Post Operative rehabilitation</li>
    <li><svg class="tick" viewBox="0 0 8 8"><circle cx="4" cy="4" r="4" fill="#8cc63f"/><path d="M3 2 L5 4 L3 6" stroke="#fff" fill="none"/></svg>Custom-made orthotics</li>
  </ul>
</section>
<div class="btn abs" style="left:317px;top:873px">More Info</div>

<section class="col abs" style="left:518px;top:708px">
  <h3>Specialised services include</h3>
  <div class="sub" style="margin-top:6px">Inhouse</div>
  <ul style="margin-top:4px">
    <li><svg class="tick" viewBox="0 0 8 8"><circle cx="4" cy="4" r="4" fill="#8cc63f"/><path d="M3 2 L5 4 L3 6" stroke="#fff" fill="none"/></svg>Runner's assessment and training</li>
    <li><svg class="tick" viewBox="0 0 8 8"><circle cx="4" cy="4" r="4" fill="#8cc63f"/><path d="M3 2 L5 4 L3 6" stroke="#fff" fill="none"/></svg>Computer Spinal/Posture Assessment</li>
  </ul>
  <div class="sub" style="margin-top:4px">Onsite visit</div>
  <ul style="margin-top:4px">
    <li><svg class="tick" viewBox="0 0 8 8"><circle cx="4" cy="4" r="4" fill="#8cc63f"/><path d="M3 2 L5 4 L3 6" stroke="#fff" fill="none"/></svg>OH&amp;S Assessment</li>
    <li><svg class="tick" viewBox="0 0 8 8"><circle cx="4" cy="4" r="4" fill="#8cc63f"/><path d="M3 2 L5 4 L3 6" stroke="#fff" fill="none"/></svg>Office workplace Assessment</li>
  </ul>
</section>
<div class="btn abs" style="left:518px;top:873px">More Info</div>

<div class="partners" aria-label="Health fund and association partners">
  <div class="partner abs" style="left:88px;width:40px;background:#1a9ad6"></div>
  <div class="partner abs" style="left:170px;width:34px;background:#2a8a44"></div>
  <div class="partner abs" style="left:246px;width:48px;background:#d8d8d8"></div>
  <div class="partner abs" style="left:331px;width:66px;background:#e0335a"></div>
  <div class="partner abs" style="left:430px;width:64px;background:#3a9a3a"></div>
  <div class="partner abs" style="left:520px;width:66px;background:#2d6db5"></div>
  <div class="partner abs" style="left:628px;width:56px;background:#c43a3a"></div>
</div>

<footer class="footer abs"></footer>
<h3 class="abs" style="left:78px;top:1036px;font-size:14.5px">Contact Us</h3>
<svg class="abs" style="left:79px;top:1076px" width="10" height="14" viewBox="0 0 10 14"><path d="M5 0 A5 5 0 0 1 10 5 Q10 8 5 14 Q0 8 0 5 A5 5 0 0 1 5 0Z" fill="#2e8b45"/><circle cx="5" cy="5" r="2" fill="#eef2cf"/></svg>
<p class="addr abs" style="left:98px;top:1074px">Shop 8, The Arcade, 212 Kestrel Ave,<br><span class="city">Harbourside 2090</span></p>
<p class="addr abs" style="left:98px;top:1118px">Shop 2, 18-20 Wattle Rd Elmwood 2118<br><span class="city">Australia</span></p>
<div class="fphone abs" style="left:348px;top:1073px"><svg width="9" height="12" viewBox="0 0 8 10"><path d="M2 0 L4 2 L3 3.5 Q4 6 5.5 6.8 L6.5 6 L8 8 L6.5 9.8 Q1 8 0 1.5Z" fill="#2e8b45"/></svg>02 9000 7623</div>
<div class="fphone abs" style="left:348px;top:1120px"><svg width="9" height="12" viewBox="0 0 8 10"><path d="M2 0 L4 2 L3 3.5 Q4 6 5.5 6.8 L6.5 6 L8 8 L6.5 9.8 Q1 8 0 1.5Z" fill="#2e8b45"/></svg>02 9000 4417</div>
<h3 class="abs" style="left:518px;top:1039px;font-size:14.5px">Opening Hours</h3>
<p class="hours abs" style="left:518px;top:1069px">Monday to Friday: 8am - 7pm<br>Saturday: 8am - 1pm</p>
<div class="appt abs">Request an Appointment</div>
<div class="copy abs">© Copyright 2014 brightlanehealth. All Rights Reserved</div>

</body>
</html>
```